Every Shelf Set Neatly or ESN Organized needs a business card design. ESN Organized is a professi

We need a business card design that is clean, sharp and conveys a sense of organization. I already have a logo.

Target Market(s)

Families (specifically mothers), small business owners, parents, seniors

Industry/Entity Type

Business

Contact Information for Business Card

My website is www.esnorganized-example.com and my Facebook page is http://www.sociallink-example.com/everyshelfsetneatly. The phone number is 418-552-7094 and I want to be listed as Lorna M. Pelham, Owner

Requirements
Must have
• My logo.

```html
<!DOCTYPE html>
<html lang="en">
<head>
<meta charset="utf-8">
<title>Every Shelf Set Neatly – Business Card</title>
<link href="https://fonts.googleapis.com/css2?family=Roboto:wght@400;700&display=swap" rel="stylesheet">
<style>
  :root {
    --backdrop: #b9a67a;
    --card-white: #ffffff;
    --card-black: #060606;
    --brand-blue: #1a82dc;
    --ink-dark: #1d1d1d;
    --ink-light: #ffffff;
  }
  * { box-sizing: border-box; margin: 0; padding: 0; }
  html, body {
    width: 1200px; height: 950px; overflow: hidden;
    background: var(--backdrop);
  }
  .sheet { position: relative; width: 1200px; height: 950px; }
  .card {
    position: absolute; left: 215px; width: 770px; height: 440px;
    overflow: hidden;
    box-shadow: 0 10px 24px rgba(0,0,0,0.25);
  }
  .card--back { top: 25px; background: var(--card-black); }
  .card--front { top: 485px; background: var(--card-white); }

  .wordmark {
    position: absolute; display: flex; align-items: center; gap: 14px;
    font-family: 'Roboto', sans-serif; font-weight: 400;
    font-size: 38px; letter-spacing: 0; white-space: nowrap;
  }
  .wordmark__mark { width: 22px; height: 22px; flex: none; background: currentColor; }
  .card--back .wordmark { left: 50%; top: 50%; transform: translate(-50%, -50%); color: var(--ink-light); }
  .card--front .wordmark { left: 50%; top: 62px; transform: translateX(-50%); color: var(--ink-dark); }

  .front-art { position: absolute; inset: 0; }

  .contact-list {
    position: absolute; left: 30px; top: 205px; list-style: none;
    font-family: 'Roboto', sans-serif; font-size: 19px; color: var(--ink-light);
  }
  .contact-list li { display: flex; align-items: center; gap: 10px; height: 28px; }
  .contact-list svg { width: 16px; height: 16px; flex: none; }

  .holder {
    position: absolute; right: 40px; top: 300px; text-align: right;
    font-family: 'Roboto', sans-serif; color: var(--ink-light);
  }
  .holder__name { font-weight: 700; font-size: 27px; }
  .holder__role { font-weight: 700; font-size: 18px; margin-top: 10px; }
</style>
</head>
<body>
<main class="sheet">
  <section class="card card--back" aria-label="Card back">
    <div class="wordmark"><span class="wordmark__mark"></span><span>Every Shelf Set Neatly</span></div>
  </section>

  <section class="card card--front" aria-label="Card front">
    <svg class="front-art" viewBox="0 0 770 440" aria-hidden="true">
      <rect x="0" y="178" width="770" height="200" fill="var(--card-black)"/>
      <path d="M418 440 V300 Q418 262 456 262 H770 V440 Z" fill="var(--card-white)"/>
      <path d="M426 416 V306 Q426 270 462 270 H770 V416 Z" fill="var(--brand-blue)"/>
    </svg>

    <div class="wordmark"><span class="wordmark__mark"></span><span>Every Shelf Set Neatly</span></div>

    <ul class="contact-list">
      <li>
        <svg viewBox="0 0 16 16"><path d="M3 1h3l1.5 4-2 1.5a9 9 0 0 0 4 4L11 8.5l4 1.5v3a2 2 0 0 1-2 2C6.5 15 1 9.5 1 3a2 2 0 0 1 2-2z" fill="var(--ink-light)"/></svg>
        <span>418-552-7094</span>
      </li>
      <li>
        <svg viewBox="0 0 16 16"><circle cx="8" cy="8" r="6.5" fill="none" stroke="var(--ink-light)" stroke-width="1.6"/><path d="M1.5 8h13M8 1.5c-3 3-3 10 0 13M8 1.5c3 3 3 10 0 13" fill="none" stroke="var(--ink-light)" stroke-width="1.2"/></svg>
        <span>www.esnorganized-example.com</span>
      </li>
      <li>
        <svg viewBox="0 0 16 16"><rect x="1" y="1" width="14" height="14" rx="2" fill="var(--ink-light)"/></svg>
        <span>everyshelfsetneatly</span>
      </li>
    </ul>

    <div class="holder">
      <p class="holder__name">Lorna M. Pelham</p>
      <p class="holder__role">Owner</p>
    </div>
  </section>
</main>
</body>
</html>
```